we can communicate on this, but i want to follow the approach we took on Pellew|Marsh & Quinlan but i feel the card front needs the black background and the platinum and gold logo. The back? I am open. we can use the same info from PM&Q. Velmont Arc is an enhanced equity investment fund - basically a very exclusive boutique hedge fund that uses only stock options. very advanced things. hope you are interested

Contact Information for Business Card

Dr. Lewis T. Brennick, CFA
Scientifique de fusée financière
701.555.0143
LTBquant47@mailvantor.com

4718 Willow Creek Bend W.
West Fargo, ND 58078

No web site

Colors

Designer to choose colors to be used in the design.

Requirements
Nice to have
• I tend to prefer the most visible applications of the logo to include logo and name, the logo version with a black background and the gold and platinum components separated by the black. I see this working well for a single side (logo and name - this is card front to me).
• I am fairly open to other treatments on the reverse side with the data. To me, it makes sense to have a different color rendition of the logo on the reverse and it may be a muted black tone on tone or an oversized portion that would have spot UV. Or, the reverse may play with colors and layout
Should not have
• Other colors = no no
• Decorative font

```html
<!DOCTYPE html>
<html lang="en">
<head>
<meta charset="utf-8">
<title>Velmont Arc – Business Card</title>
<link href="https://fonts.googleapis.com/css2?family=Montserrat:wght@400;600;700&display=swap" rel="stylesheet">
<style>
  :root {
    --stage: #161616;
    --stage-edge: #0b0b0b;
    --card: #1e1e1e;
    --card-light: #2c2c2c;
    --gold: #c9a227;
    --platinum: #c9c9cc;
    --white: #f4f4f4;
    --tone-dark: #1c1c1c;
    --tone-mid: #333333;
    --tone-light: #5c5c5c;
  }
  * { margin: 0; padding: 0; box-sizing: border-box; }
  html, body {
    width: 1200px;
    height: 900px;
    overflow: hidden;
  }
  body {
    background: radial-gradient(ellipse at 50% 40%, var(--stage) 0%, var(--stage-edge) 100%);
    font-family: "Montserrat", Arial, sans-serif;
    color: var(--white);
    position: relative;
  }
  .card {
    position: absolute;
    left: 250px;
    width: 700px;
    height: 400px;
    border-radius: 4px;
    box-shadow: 0 18px 40px rgba(0, 0, 0, 0.6);
    overflow: hidden;
  }

  /* Reverse side */
  .card-back { top: 30px; }
  .tone-field {
    position: absolute;
    inset: 0;
    background:
      radial-gradient(circle at 50% 50%, rgba(255,255,255,0.05) 0%, rgba(255,255,255,0) 45%),
      linear-gradient(110deg, var(--tone-dark) 0%, var(--tone-mid) 50%, var(--tone-light) 100%);
  }
  .back-mark {
    position: absolute;
    left: 50%;
    top: 50%;
    transform: translate(-50%, -50%);
    display: flex;
    align-items: center;
    gap: 12px;
  }
  .back-mark-dot {
    width: 30px;
    height: 30px;
    border-radius: 50%;
    background: var(--gold);
  }
  .back-mark-name {
    font-weight: 600;
    font-size: 16px;
    letter-spacing: 3px;
    color: var(--platinum);
    text-transform: uppercase;
  }

  /* Front side */
  .card-front {
    top: 460px;
    background: linear-gradient(120deg, var(--card) 0%, var(--card) 55%, var(--card-light) 100%);
    display: flex;
    align-items: center;
  }
  .brand {
    width: 300px;
    display: flex;
    flex-direction: column;
    align-items: center;
    gap: 20px;
  }
  .brand-dot {
    width: 100px;
    height: 100px;
    border-radius: 50%;
    background: var(--gold);
  }
  .brand-name {
    font-weight: 700;
    font-size: 32px;
    letter-spacing: 1px;
    color: var(--white);
    text-transform: uppercase;
  }
  .divider {
    width: 2px;
    height: 210px;
    background: var(--gold);
    flex: none;
  }
  .details {
    padding-left: 32px;
    padding-right: 20px;
  }
  .person-name {
    font-weight: 600;
    font-size: 18px;
    letter-spacing: 0.6px;
    color: var(--gold);
    text-transform: uppercase;
    white-space: nowrap;
  }
  .person-title {
    font-size: 15px;
    font-weight: 400;
    letter-spacing: 0.5px;
    margin-top: 4px;
    margin-bottom: 18px;
  }
  .address {
    font-size: 16px;
    line-height: 1.4;
    letter-spacing: 0.5px;
    margin-bottom: 14px;
  }
  .contact-list {
    list-style: none;
    font-size: 16px;
    line-height: 1.6;
    letter-spacing: 0.5px;
  }
  .contact-list li {
    display: flex;
    align-items: center;
    gap: 10px;
    white-space: nowrap;
  }
  .contact-icon {
    width: 14px;
    height: 14px;
    flex: none;
  }
</style>
</head>
<body>

  <section class="card card-back">
    <div class="tone-field" role="img" aria-label="Tone-on-tone spot UV brand pattern across the reverse side"></div>
    <div class="back-mark">
      <div class="back-mark-dot"></div>
      <div class="back-mark-name">Velmont Arc</div>
    </div>
  </section>

  <section class="card card-front">
    <div class="brand">
      <div class="brand-dot"></div>
      <div class="brand-name">Velmont Arc</div>
    </div>
    <div class="divider"></div>
    <div class="details">
      <p class="person-name">Dr. Lewis T. Brennick, CFA</p>
      <p class="person-title">Scientifique de fusée financière</p>
      <p class="address">4718 Willow Creek Bend W.<br>West Fargo, ND 58078</p>
      <ul class="contact-list">
        <li>
          <svg class="contact-icon" viewBox="0 0 16 16" aria-hidden="true">
            <path d="M4 1.5 L6.2 4.5 L5 6.2 C5.8 8 7.8 10 9.8 11 L11.5 9.8 L14.5 12 L13 14.5 C7.5 14 2 8.5 1.5 3 Z" fill="var(--gold)"/>
          </svg>
          701.555.0143
        </li>
        <li>
          <svg class="contact-icon" viewBox="0 0 16 16" aria-hidden="true">
            <rect x="1.5" y="3.5" width="13" height="9" fill="none" stroke="var(--gold)" stroke-width="1.4"/>
            <path d="M1.5 3.5 L8 9 L14.5 3.5" fill="none" stroke="var(--gold)" stroke-width="1.4"/>
          </svg>
          LTBquant47@mailvantor.com
        </li>
      </ul>
    </div>
  </section>

</body>
</html>
```